Tallwick Home Services Web Site

Design Web site with 3-4 pages: Home, About Us, Services and Order form / Schedule Appointment (which will likely be link to Method App and Quickbooks integration.)
Services include: Dryer Vent Cleaning, AC Cleaning, Difficult-to-Reach Light Bulb replacement, Wood Repair and Home Maintenance Plans including Fire Safety Checks and Filter Replacement.

Target Market(s)

Luxury Home Owners, Professionals (Dr's/lawyers) and Seniors

Industry/Entity Type

Home Maintenance

Coding

Coded - Design and coding required

Requirements
Must have
• Tagline - Where Home Maintenance is Elementary

```html
<!DOCTYPE html>
<html lang="en">
<head>
<meta charset="utf-8">
<title>Tallwick Home Services</title>
<link href="https://fonts.googleapis.com/css2?family=Montserrat:wght@500;600;700&family=Questrial&display=swap" rel="stylesheet">
<style>
:root{
  --gold:#d9a42b;
  --gold-light:#f3c54f;
  --cream:#faf4e3;
  --ink:#222222;
  --dark:#232323;
  --white:#ffffff;
  --line:#cfd3d6;
  --navy:#2d3a5c;
}
*{margin:0;padding:0;box-sizing:border-box}
html,body{width:1200px;height:3429px;overflow:hidden}
body{position:relative;font-family:"Questrial",sans-serif;color:var(--ink);background:var(--white)}
.abs{position:absolute}
.heading{font-family:"Montserrat",sans-serif;font-weight:600;letter-spacing:-.5px}

/* hero */
.hero-photo{left:0;top:0;width:1200px;height:600px;background:linear-gradient(180deg,#4b5666 0%,#6f7a84 35%,#9aa29a 60%,#4f6b3a 85%,#3c4f2c 100%)}
.hero-curve{left:0;top:440px;width:1200px;height:680px}
.brand{left:112px;top:40px;display:flex;align-items:center;gap:10px;color:var(--white);font-family:"Montserrat",sans-serif;font-weight:600;font-size:15px;line-height:1.15;letter-spacing:1px}
.brand .dot{width:26px;height:26px;border-radius:50%;background:var(--white)}
.nav{top:62px;font-family:"Montserrat",sans-serif;font-weight:500;font-size:14px;color:var(--white)}
.nav.active{color:var(--gold)}
.btn{display:flex;align-items:center;justify-content:space-between;border-radius:30px;font-family:"Montserrat",sans-serif;font-weight:500;font-size:13px}
.btn .chev{width:26px;height:26px;border-radius:50%;display:flex;align-items:center;justify-content:center}
.btn-white{background:var(--white);color:var(--ink)}
.btn-white .chev{background:var(--gold)}
.hero-title{left:0;width:1200px;top:420px;font-size:34px;color:var(--white);text-align:center}

/* about */
.mission{left:110px;top:634px;width:520px;font-size:14.5px;line-height:33px;color:var(--white)}
.about-photo{left:110px;top:738px;width:556px;height:294px;border-radius:18px;background:linear-gradient(120deg,#e6ebf0 0%,#c9d3dc 45%,#3a62a8 70%,#8a8c90 100%)}
.about-title{right:110px;top:636px;font-size:30px;color:var(--white)}
.rule{height:2px;background:var(--ink)}
.about-sub{right:110px;top:716px;text-align:right;font-size:19px;line-height:33px;color:var(--white)}
.about-text{right:110px;top:797px;width:372px;text-align:right;font-size:15px;line-height:33.5px;color:var(--white)}

/* services */
.sec-title{left:0;width:1200px;text-align:center;font-size:30px;color:var(--gold)}
.card{top:1293px;width:307px;height:456px;border-radius:16px;overflow:hidden}
.card .tag{position:absolute;left:53px;background:var(--white);border-radius:10px;display:flex;align-items:center;gap:14px;padding:0 14px;font-family:"Montserrat",sans-serif;font-weight:500;font-size:14px}
.card .ico{width:36px;height:36px;flex:none}
.card .arrow{margin-left:auto;width:40px;height:40px;border-radius:50%;border:1px solid var(--line);display:flex;align-items:center;justify-content:center}
.btn-gold{background:var(--gold);color:var(--white);font-size:15px}
.btn-gold .chev{background:var(--white)}

/* why */
.why-bg{left:0;top:1932px;width:1200px;height:634px;background:var(--cream);border-radius:48px 48px 0 0}
.why-head{font-family:"Montserrat",sans-serif;font-weight:600;font-size:18px;color:var(--gold);text-align:center;width:320px}
.why-text{font-size:15px;line-height:33px;color:#4a4a4a;text-align:center;width:320px}
.why-circle{width:144px;height:144px;border-radius:50%;background:linear-gradient(180deg,var(--gold) 0%,var(--gold-light) 100%);display:flex;align-items:center;justify-content:center}

/* testimonial */
.quote{left:0;width:1200px;top:2766px;text-align:center;font-size:15.5px;line-height:35px}
.who{left:0;width:1200px;top:2856px;text-align:center;font-family:"Montserrat",sans-serif;font-weight:500;font-size:15px;color:var(--gold)}

/* footer */
.footer{left:0;top:3001px;width:1200px;height:428px;background:var(--dark)}
.f-col{width:320px;text-align:center}
.f-ico{width:46px;height:46px;border-radius:50%;background:var(--gold);margin:0 auto;display:flex;align-items:center;justify-content:center}
.f-label{margin-top:34px;font-family:"Montserrat",sans-serif;font-weight:500;font-size:17px;color:var(--gold)}
.f-info{margin-top:18px;font-family:"Montserrat",sans-serif;font-weight:500;font-size:14px;color:var(--white)}
.f-links{right:133px;font-family:"Montserrat",sans-serif;font-weight:500;font-size:13.5px;color:var(--white);word-spacing:2px}
.f-links span{margin:0 14px}
.social{top:3352px;width:28px;height:28px;border-radius:50%;border:1px solid #777}
.social.on{background:var(--gold);border-color:var(--gold)}
.f-brand{left:113px;top:3280px;display:flex;align-items:center;gap:14px;color:var(--gold);font-family:"Montserrat",sans-serif;font-weight:600;font-size:24px;line-height:1.15;letter-spacing:1.5px}
.f-brand .dot{width:40px;height:40px;border-radius:50%;background:var(--gold)}
</style>
</head>
<body>

<!-- hero -->
<div class="abs hero-photo" role="img" aria-label="Photo of a white two-storey house with dark roof under a cloudy sky, trees around"></div>
<svg class="abs hero-curve" width="1200" height="680" viewBox="0 0 1200 680" aria-hidden="true">
  <path d="M0 15 Q600 220 1200 15 L1200 675 L0 675 Z" fill="#d9a42b"/>
</svg>
<div class="abs brand"><span class="dot"></span><span>TALLWICK<br>HOME SERVICES</span></div>
<div class="abs nav active" style="left:417px">HOME</div>
<div class="abs nav" style="left:486px">ABOUT US</div>
<div class="abs nav" style="left:586px">OUR SERVICES</div>
<div class="abs nav" style="left:715px">CONTACT US</div>
<div class="abs btn btn-white" style="left:846px;top:51px;width:241px;height:38px;padding:0 6px 0 24px">SCHEDULE APPOINTMENT<span class="chev"><svg width="12" height="12" viewBox="0 0 12 12"><path d="M2 2l4 4-4 4M6 2l4 4-4 4" stroke="#fff" stroke-width="1.6" fill="none"/></svg></span></div>
<h1 class="abs heading hero-title">WHERE HOME MAINTENANCE IS ELEMENTARY</h1>

<!-- about -->
<p class="abs mission">Our mission is simple: to keep your home safe, comfortable, and running smoothly, so you can enjoy peace of mind every day.</p>
<div class="abs about-photo" role="img" aria-label="Photo of a technician in a blue cap and gloves cleaning a wall-mounted air conditioner"></div>
<h2 class="abs heading about-title">ABOUT TALLWICK HOMES</h2>
<div class="abs rule" style="left:1033px;top:686px;width:57px"></div>
<h3 class="abs heading about-sub">YOUR TRUSTED PARTNER IN<br>HOME CARE</h3>
<p class="abs about-text">At Tallwick Homes, we believe that a well-maintained home is a happy home. With years of experience in home maintenance and repair, we have built a reputation for reliability, thoroughness, and exceptional customer service.</p>
<div class="abs btn btn-white" style="left:932px;top:993px;width:156px;height:38px;padding:0 6px 0 22px">LEARN MORE<span class="chev"><svg width="12" height="12" viewBox="0 0 12 12"><path d="M2 2l4 4-4 4M6 2l4 4-4 4" stroke="#fff" stroke-width="1.6" fill="none"/></svg></span></div>

<!-- services -->
<h2 class="abs heading sec-title" style="top:1188px">TALLWICK SERVICES</h2>
<div class="abs rule" style="left:571px;top:1237px;width:57px"></div>

<div class="abs card" style="left:110px" role="img" aria-label="Photo of a technician cleaning a dryer vent beside a washing machine">
  <div style="position:absolute;inset:0;background:linear-gradient(160deg,#cfd5d2 0%,#8f9aa1 45%,#2e4f8f 75%,#4a4a4a 100%)"></div>
  <div class="tag" style="top:358px;width:245px;height:88px">
    <svg class="ico" viewBox="0 0 36 36"><path d="M4 8h14v8H4zM18 12h10v18M10 16v14" stroke="#d9a42b" stroke-width="2" fill="none"/></svg>
    <span>DRYER VENT<br>CLEANING</span>
    <span class="arrow"><svg width="12" height="12" viewBox="0 0 12 12"><path d="M2 10L10 2M4 2h6v6" stroke="#222" stroke-width="1.5" fill="none"/></svg></span>
  </div>
</div>

<div class="abs card" style="left:446px" role="img" aria-label="Photo of a technician servicing a wall air conditioner">
  <div style="position:absolute;inset:0;background:linear-gradient(160deg,#e4e8ec 0%,#c2cbd3 45%,#2f4f8c 80%,#3b3b3b 100%)"></div>
  <div class="tag" style="top:255px;width:242px;height:188px;flex-direction:column;align-items:stretch;gap:0;padding:16px 18px 0">
    <div style="display:flex;align-items:center;gap:14px;height:44px;border-bottom:1px solid #e1e1e1;padding-bottom:12px;box-sizing:content-box">
      <svg class="ico" style="width:30px;height:30px" viewBox="0 0 36 36"><rect x="4" y="6" width="28" height="12" rx="2" stroke="#d9a42b" stroke-width="2" fill="none"/><path d="M10 22v8M18 22v8M26 22v8" stroke="#d9a42b" stroke-width="2"/></svg>
      <span>AC CLEANING</span>
    </div>
    <p style="font-family:Questrial,sans-serif;font-size:15px;line-height:31px;margin-top:10px;width:185px">Breathe cleaner air and enjoy optimal cooling all year round.</p>
  </div>
</div>

<div class="abs card" style="left:781px" role="img" aria-label="Photo of a hand applying wood filler to a cracked wooden board in a workshop">
  <div style="position:absolute;inset:0;background:linear-gradient(160deg,#5e4a3a 0%,#8a6a4c 45%,#b58c62 75%,#7a5a3e 100%)"></div>
  <div class="tag" style="top:358px;width:245px;height:88px">
    <svg class="ico" viewBox="0 0 36 36"><path d="M4 30h28M8 30V12h12v18M20 18h8v12" stroke="#d9a42b" stroke-width="2" fill="none"/></svg>
    <span>WOOD REPAIR</span>
    <span class="arrow"><svg width="12" height="12" viewBox="0 0 12 12"><path d="M2 10L10 2M4 2h6v6" stroke="#222" stroke-width="1.5" fill="none"/></svg></span>
  </div>
</div>

<div class="abs btn btn-gold" style="left:505px;top:1805px;width:189px;height:42px;padding:0 8px 0 20px">VIEW SERVICES<span class="chev"><svg width="12" height="12" viewBox="0 0 12 12"><path d="M2 2l4 4-4 4M6 2l4 4-4 4" stroke="#d9a42b" stroke-width="1.6" fill="none"/></svg></span></div>

<!-- why choose -->
<div class="abs why-bg"></div>
<h2 class="abs heading sec-title" style="top:1990px">WHY CHOOSE TALLWICK HOMES</h2>
<div class="abs rule" style="left:571px;top:2038px;width:57px"></div>

<div class="abs" style="left:90px;top:2083px">
  <div class="why-head">EXPERIENCED TECHNICIANS</div>
  <div class="why-text" style="margin-top:8px">Our skilled team is trained to handle<br>every type of home maintenance</div>
</div>
<div class="abs" style="left:544px;top:2083px">
  <div class="why-head">COMPREHENSIVE SOLUTIONS</div>
  <div class="why-text" style="margin-top:8px">From dryer vent cleaning to full home<br>maintenance plans</div>
</div>

<svg class="abs" style="left:0;top:2150px" width="1200" height="290" viewBox="0 0 1200 290" aria-hidden="true">
  <g stroke="#cfd3d6" stroke-width="1.5" fill="none">
    <path d="M138 60 V143 A113 113 0 0 0 364 143"/>
    <path d="M364 143 A113 113 0 0 1 591 143"/>
    <path d="M591 143 A113 113 0 0 0 815 143"/>
    <path d="M815 143 A113 113 0 0 1 1042 143 V225"/>
  </g>
  <g fill="#2d3a5c">
    <circle cx="138" cy="143" r="5"/><circle cx="364" cy="143" r="5"/><circle cx="591" cy="143" r="5"/><circle cx="815" cy="143" r="5"/><circle cx="1042" cy="143" r="5"/>
  </g>
</svg>

<div class="abs why-circle" style="left:178px;top:2221px"><svg width="64" height="64" viewBox="0 0 64 64" fill="none" stroke="#fff" stroke-width="2.5"><path d="M20 26a12 12 0 0 1 24 0M16 26h32"/><circle cx="26" cy="44" r="8"/><path d="M38 50l12-12"/></svg></div>
<div class="abs why-circle" style="left:403px;top:2221px"><svg width="64" height="64" viewBox="0 0 64 64" fill="none" stroke="#fff" stroke-width="2.5"><path d="M32 8l16 6v12c0 10-7 16-16 20-9-4-16-10-16-20V14z"/><path d="M24 26l6 6 10-12"/><path d="M12 44l12 10h16l12-10"/></svg></div>
<div class="abs why-circle" style="left:632px;top:2221px"><svg width="64" height="64" viewBox="0 0 64 64" fill="none" stroke="#fff" stroke-width="2.5"><circle cx="32" cy="26" r="12"/><path d="M26 40h12v8H26zM14 26h4M46 26h4M32 6v4"/></svg></div>
<div class="abs why-circle" style="left:858px;top:2221px"><svg width="64" height="64" viewBox="0 0 64 64" fill="none" stroke="#fff" stroke-width="2.5"><path d="M32 8l14 5v11c0 9-6 14-14 18-8-4-14-9-14-18V13z"/><path d="M32 18v14M25 25h14"/><path d="M10 36v12l10 8M54 36v12l-10 8"/></svg></div>

<div class="abs" style="left:315px;top:2405px">
  <div class="why-head">RELIABLE &amp; ON-TIME SERVICE</div>
  <div class="why-text" style="margin-top:8px">We value your time. Our team arrives<br>promptly and completes work</div>
</div>
<div class="abs" style="left:770px;top:2405px">
  <div class="why-head">SAFETY FIRST</div>
  <div class="why-text" style="margin-top:8px">Your home and family's safety is our<br>top priority. All work is performed</div>
</div>

<!-- testimonials -->
<h2 class="abs heading sec-title" style="top:2640px">WHAT OUR CUSTOMERS SAY</h2>
<div class="abs rule" style="left:571px;top:2688px;width:57px"></div>
<svg class="abs" style="left:553px;top:2728px" width="94" height="18" viewBox="0 0 94 18" aria-label="Five stars">
  <g fill="#f0c23a" stroke="#444" stroke-width=".8">
    <path id="st" d="M9 1l2.4 5 5.4.6-4 3.7 1.1 5.4L9 13l-4.9 2.7 1.1-5.4-4-3.7 5.4-.6z"/>
    <use href="#st" x="19"/><use href="#st" x="38"/><use href="#st" x="57"/><use href="#st" x="76"/>
  </g>
</svg>
<p class="abs quote">"Tallwick Homes did an amazing job cleaning our dryer vent. The team was professional, fast, and explained<br>everything clearly. I feel much safer knowing it's done right!"</p>
<div class="abs who">DANA M., HOMEOWNER</div>
<svg class="abs" style="left:555px;top:2907px" width="90" height="14" viewBox="0 0 90 14" aria-hidden="true">
  <g stroke="#d9a42b" stroke-width="1.2" fill="none"><circle cx="6" cy="7" r="4"/><circle cx="58" cy="7" r="4"/><circle cx="84" cy="7" r="4"/></g>
  <circle cx="32" cy="7" r="4.5" fill="#d9a42b"/>
</svg>

<!-- footer -->
<div class="abs footer"></div>
<div class="abs f-col" style="left:67px;top:3051px">
  <div class="f-ico"><svg width="18" height="18" viewBox="0 0 18 18"><path d="M4 2l3 3-2 2c1 2 2.5 3.5 4.5 4.5l2-2 3 3-2 2.5C7 14 4 11 1.5 4.5z" fill="#fff"/></svg></div>
  <div class="f-label">CALL US</div><div class="f-info">+1 555 014 2290</div>
</div>
<div class="abs f-col" style="left:392px;top:3051px">
  <div class="f-ico"><svg width="18" height="14" viewBox="0 0 18 14"><rect x="1" y="1" width="16" height="12" rx="1.5" fill="#fff"/><path d="M1.5 2l7.5 6 7.5-6" stroke="#d9a42b" stroke-width="1.4" fill="none"/></svg></div>
  <div class="f-label">EMAIL US</div><div class="f-info">INFO@TALLWICKHOME.COM</div>
</div>
<div class="abs f-col" style="left:766px;top:3051px">
  <div class="f-ico"><svg width="16" height="20" viewBox="0 0 16 20"><path d="M8 1a6.5 6.5 0 0 1 6.5 6.5C14.5 12 8 19 8 19S1.5 12 1.5 7.5A6.5 6.5 0 0 1 8 1z" fill="#fff"/><circle cx="8" cy="7.5" r="2.5" fill="#d9a42b"/></svg></div>
  <div class="f-label">REACH US</div><div class="f-info">48, 210 ELM AVENUE, 553 120</div>
</div>
<div class="abs" style="left:110px;top:3226px;width:982px;height:1px;background:#3a3a3a"></div>
<div class="abs f-brand"><span class="dot"></span><span>TALLWICK<br>HOME SERVICES</span></div>
<div class="abs f-links" style="top:3259px">HOME<span>/</span>ABOUT US<span>/</span>OUR SERVICES<span>/</span>CONTACT US</div>
<div class="abs f-links" style="top:3304px">@2025 COPYRIGHTS<span>/</span>ALL RIGHTS RESERVED</div>
<div class="abs social" style="left:942px" aria-label="Social profile"></div>
<div class="abs social on" style="left:990px" aria-label="Social profile"></div>
<div class="abs social" style="left:1037px" aria-label="Social profile"></div>

</body>
</html>
```